Personal training and nutrition business needs business card design

We need a business card that outlays our services and invites potential customers to join our team and take the first step to a healthier and more enjoyable life. We cater for any level of fitness and specialize in weight loss and conditioning, strength training, muscle gain and strength endurance. Whether you are just starting off or need some help getting to the next level of your journey we are here to get the job done.
We specialize in one on one or one on two personal training sessions and each program will be custom made to suit individual fitness goals of our clients

```html
<!DOCTYPE html>
<html lang="en">
<head>
<meta charset="utf-8">
<title>Drive &amp; Rhythm — Business Card</title>
<link rel="stylesheet" href="https://fonts.googleapis.com/css2?family=Archivo:wght@400;600;800;900&family=Oswald:wght@500&display=swap">
<style>
  :root {
    --stage: #2b2b2b;
    --card: #050505;
    --card-back: #080808;
    --purple: #9b5cd6;
    --purple-deep: #7b4bc4;
    --white: #f2f2f2;
    --grey: #d9d9d9;
    --faint: #1f1f1f;
    --divider: #3a3a3a;
  }
  * { box-sizing: border-box; margin: 0; padding: 0; }
  html, body {
    width: 1200px; height: 1040px; overflow: hidden;
    background: var(--stage);
    font-family: "Archivo", Arial, sans-serif;
  }
  .canvas { position: relative; width: 1200px; height: 1040px; }

  .card {
    position: absolute; left: 230px; width: 740px; height: 420px;
    background: var(--card);
    box-shadow: 0 18px 40px rgba(0,0,0,.45);
  }
  .card--back {
    top: 70px; background: var(--card-back);
    border-radius: 90px 0 90px 0;
    display: flex; flex-direction: column; align-items: center; justify-content: center; gap: 22px;
  }
  .card--front {
    top: 550px;
    border-radius: 0 90px 0 90px;
  }

  .back-mark {
    width: 120px; height: 120px; border-radius: 50%;
    background: var(--faint);
  }
  .back-name {
    font-weight: 900; font-size: 64px; line-height: .95; letter-spacing: 2px;
    text-transform: uppercase; color: var(--faint); text-align: center;
  }

  .brand {
    position: absolute; left: 80px; top: 70px; width: 300px;
    display: flex; flex-direction: column; align-items: center;
  }
  .brand-mark {
    width: 96px; height: 96px; border-radius: 50%;
    background: linear-gradient(135deg, var(--purple-deep), #c86fd6);
  }
  .brand-name {
    margin-top: 18px;
    font-weight: 900; font-size: 44px; line-height: .95; letter-spacing: 1px;
    text-transform: uppercase; color: var(--white); text-align: center;
  }
  .brand-services {
    margin-top: 10px;
    font-family: "Oswald", "Arial Narrow", sans-serif; font-weight: 500;
    font-size: 12px; letter-spacing: 1px; text-transform: uppercase; color: var(--purple);
  }

  .divider {
    position: absolute; left: 410px; top: 80px; width: 1px; height: 200px;
    background: var(--divider);
  }

  .contact { position: absolute; left: 440px; top: 95px; color: var(--grey); }
  .contact-name {
    font-weight: 600; font-size: 28px; color: var(--purple); text-transform: uppercase;
  }
  .contact-role { font-size: 19px; margin-top: 2px; }
  .contact-list { list-style: none; margin-top: 22px; font-size: 20px; }
  .contact-list li { display: flex; align-items: center; gap: 10px; margin-bottom: 6px; }
  .contact-list svg { width: 20px; height: 20px; flex: none; }
  .contact-address { margin-top: 22px; font-size: 20px; }

  .motto {
    position: absolute; left: 0; right: 0; bottom: 50px; text-align: center;
    font-weight: 900; font-size: 30px; letter-spacing: 2px; color: var(--purple);
  }
</style>
</head>
<body>
<main class="canvas">
  <section class="card card--back" aria-label="Card back">
    <div class="back-mark"></div>
    <p class="back-name">Drive &amp;<br>Rhythm</p>
  </section>

  <section class="card card--front" aria-label="Card front">
    <div class="brand">
      <div class="brand-mark"></div>
      <p class="brand-name">Drive &amp;<br>Rhythm</p>
      <p class="brand-services">Personal training. Nutrition. Motivation</p>
    </div>

    <div class="divider"></div>

    <div class="contact">
      <p class="contact-name">Marcus Delaney</p>
      <p class="contact-role">Owner</p>
      <ul class="contact-list">
        <li>
          <svg viewBox="0 0 24 24" fill="none" stroke="#9b5cd6" stroke-width="2" stroke-linecap="round" stroke-linejoin="round"><path d="M22 16.9v3a2 2 0 0 1-2.2 2 19.8 19.8 0 0 1-8.6-3.1 19.5 19.5 0 0 1-6-6A19.8 19.8 0 0 1 2.1 4.2 2 2 0 0 1 4.1 2h3a2 2 0 0 1 2 1.7c.1 1 .4 1.9.7 2.8a2 2 0 0 1-.5 2.1L8 9.9a16 16 0 0 0 6 6l1.3-1.3a2 2 0 0 1 2.1-.4c.9.3 1.8.6 2.8.7a2 2 0 0 1 1.8 2z"/></svg>
          <span>0400 182 736</span>
        </li>
        <li>
          <svg viewBox="0 0 24 24" fill="#9b5cd6"><path d="M2 5h20v14H2z"/><path d="M2 5l10 8 10-8" fill="none" stroke="#050505" stroke-width="1.6"/></svg>
          <span>driveandrhythmpt@mail.com</span>
        </li>
      </ul>
      <p class="contact-address">14 Larch St Kensington vic 3031</p>
    </div>

    <p class="motto">COMMIT. PERFORM. SUCCEED</p>
  </section>
</main>
</body>
</html>
```